New Bicycle shop business card

Hi!
I'm looking for a business card for my new proffesional bike mechanics shop. This shop is only for fixing broken bikes and not selling bikes.
Peferbly a modern and sleek and modern design.
Colors: black, grey, red, white
Information:
Name: Rijwielwerkplaats Vanhoutte
Shop owner: Bart Vanhoutte & Marieke Segers
Website: www.rijwielwerkplaats-vanhoutte.be
Email: info@rijwielwerkplaats-vanhoutte.be
Phone number: +32471902368
Street adres: Kerkweg 46
9940 Bellebeke
Slogan/shop information: Herstellingen van alle merken.
Logo: see files.
Target Market(s)
People who seek a mechanic to fix or upgrade their bikes.
Contact Information for Business Card
Information:
Website: info@rijwielwerkplaats-vanhoutte.be
9940 Bellebeke
Logo: see files.

```html
<!DOCTYPE html>
<html lang="nl">
<head>
<meta charset="utf-8">
<title>Rijwielwerkplaats Vanhoutte – visitekaartje</title>
<link rel="stylesheet" href="https://fonts.googleapis.com/css2?family=Open+Sans:wght@400;600;700;800&display=swap">
<style>
  :root {
    --bg: #4a4a4d;
    --card: #060607;
    --red: #ee2a48;
    --white: #ffffff;
    --grey: #a8a9aa;
  }
  * { margin: 0; padding: 0; box-sizing: border-box; }
  html, body { width: 1200px; height: 1000px; overflow: hidden; }
  body {
    background: var(--bg);
    font-family: "Open Sans", sans-serif;
    color: var(--white);
    position: relative;
  }
  .card {
    position: absolute;
    left: 220px;
    width: 760px;
    height: 430px;
    background: var(--card);
    border-radius: 22px;
    overflow: hidden;
    box-shadow: 0 14px 30px rgba(0,0,0,.45);
  }
  .card::after {
    content: "";
    position: absolute;
    left: 0; right: 0; bottom: 0;
    height: 14px;
    background: var(--red);
  }
  .card-front { top: 40px; }
  .card-back { top: 510px; }

  /* brand mark */
  .brand {
    display: flex;
    align-items: center;
    gap: 14px;
  }
  .brand-dot {
    width: 26px; height: 26px;
    border-radius: 50%;
    background: var(--red);
    flex: none;
  }
  .brand-name {
    font-weight: 800;
    text-transform: uppercase;
    letter-spacing: .06em;
    line-height: 1.15;
    color: var(--white);
  }
  .card-front .brand {
    position: absolute;
    left: 0; right: 0; top: 150px;
    justify-content: center;
  }
  .card-front .brand-name { font-size: 30px; text-align: center; }
  .tagline {
    position: absolute;
    left: 0; right: 0; top: 330px;
    text-align: center;
    font-size: 17px;
    font-weight: 600;
    letter-spacing: .02em;
  }

  /* back side */
  .owners { position: absolute; left: 50px; top: 48px; }
  .owners-label { color: var(--red); font-size: 20px; font-weight: 600; }
  .owners-names { font-size: 21px; font-weight: 700; margin-top: 2px; }

  .card-back .brand {
    position: absolute;
    right: 46px; top: 120px;
  }
  .card-back .brand-name { font-size: 22px; text-align: right; }

  .contact { position: absolute; left: 50px; top: 215px; }
  .company { color: var(--red); font-size: 22px; font-weight: 700; }
  .role { font-size: 15px; font-weight: 600; margin: 2px 0 10px; }
  .contact-list { list-style: none; }
  .contact-list li {
    display: flex; align-items: center; gap: 10px;
    font-size: 15px; line-height: 1.6;
  }
  .contact-list svg { width: 14px; height: 14px; fill: var(--red); flex: none; }

  .divider {
    position: absolute;
    left: 300px; right: 46px; top: 300px;
    height: 2px;
    background: var(--red);
  }
  .address {
    position: absolute;
    right: 46px; top: 340px;
    font-size: 18px;
    letter-spacing: .02em;
  }
</style>
</head>
<body>

<section class="card card-front">
  <div class="brand">
    <span class="brand-dot"></span>
    <span class="brand-name">Rijwielwerkplaats<br>Vanhoutte</span>
  </div>
  <p class="tagline">Herstellingen van alle merken.</p>
</section>

<section class="card card-back">
  <div class="owners">
    <p class="owners-label">Shop owner:</p>
    <p class="owners-names">Bart Vanhoutte &amp; Marieke Segers</p>
  </div>

  <div class="brand">
    <span class="brand-dot"></span>
    <span class="brand-name">Rijwielwerkplaats<br>Vanhoutte</span>
  </div>

  <div class="contact">
    <p class="company">Rijwielwerkplaats Vanhoutte</p>
    <p class="role">General Manager</p>
    <ul class="contact-list">
      <li>
        <svg viewBox="0 0 24 24" aria-hidden="true"><path d="M6.6 10.8a15.1 15.1 0 0 0 6.6 6.6l2.2-2.2c.3-.3.7-.4 1-.2 1.1.4 2.3.6 3.6.6.6 0 1 .4 1 1V20c0 .6-.4 1-1 1A17 17 0 0 1 3 4c0-.6.4-1 1-1h3.5c.6 0 1 .4 1 1 0 1.3.2 2.5.6 3.6.1.3 0 .7-.2 1z"/></svg>
        +32471902368
      </li>
      <li>
        <svg viewBox="0 0 24 24" aria-hidden="true"><path d="M2 5h20v14H2zm2 2v.5l8 5 8-5V7l-8 5z"/></svg>
        info@rijwielwerkplaats-vanhoutte.be
      </li>
      <li>
        <svg viewBox="0 0 24 24" aria-hidden="true"><path d="M12 2a10 10 0 1 0 0 20 10 10 0 0 0 0-20zm-1 17.9A8 8 0 0 1 4.2 10L9 15v1a2 2 0 0 0 2 2zm6.9-2.5A2 2 0 0 0 16 16h-1v-3a1 1 0 0 0-1-1H8v-2h2a1 1 0 0 0 1-1V7h2a2 2 0 0 0 2-2v-.4a8 8 0 0 1 2.9 12.8z"/></svg>
        www.rijwielwerkplaats-vanhoutte.be
      </li>
    </ul>
  </div>

  <div class="divider"></div>
  <p class="address">Kerkweg 46 9940 Bellebeke</p>
</section>

</body>
</html>
```